Korrabel Ice Creamery tourist signage

We need to give passing tourists a snapshot of what great fun they can have visiting our brand new Ice creamery located in Timboon, 17km North of the Great Ocean Road and Famous 12 Apostles in Victoria Australia. So the sign needs to be more than directional, need to be enticing. needs to be designed in a manner that project quality. ( keep in mind cars travelling at 80km don't have a lot of time to read too much)
Size is 2.2metres wide by 1.4 meters high
This sign needs to be succinct. Needs to convey fun and a little indulgence but not in a 'tacky' or 'cheap' way.
Needs to offer indulgent imagery of course, our logo too and direction.

Target Market(s)

Tourists, domestic and internationals

Industry/Entity Type

Tourism

Font styles to use
Other font styles liked:
• sacred cow

Colors
add136
fdf3f8
b8a6cd
fabb94
fcca95
85acd3
fbf289

Requirements
Must have
• Convey fun, whimsy indulgence and value ( keeping in mind we need to entice these people a further 17km up the road!)
Nice to have
• White space and clear imagery with
Should not have
• Bold bling colours, be busy looking and cheap looking, needs to convey quality .

```html
<!DOCTYPE html>
<html lang="en">
<head>
<meta charset="UTF-8">
<title>Korrabel Ice Creamery – Tourist Sign</title>
<link rel="stylesheet" href="https://fonts.googleapis.com/css2?family=Fredoka:wght@600&display=swap">
<style>
  :root {
    --backdrop: #e6e4e8;
    --sign-white: #f3f3f3;
    --lime: #add136;
    --butter: #fbf289;
    --ink: #2f2d2e;
    --grape: #7a16cf;
    --grape-light: #9b2bf0;
    --photo-chocolate: #5a3a33;
    --photo-peach: #fabb94;
    --photo-berry: #e23c78;
    --photo-lemon: #f7cf3f;
    --photo-plum: #6c4a8c;
    --photo-sky: #85acd3;
  }
  * { margin: 0; padding: 0; box-sizing: border-box; }
  html, body {
    width: 1200px;
    height: 886px;
    overflow: hidden;
    background: var(--backdrop);
    font-family: "Fredoka", "Arial Rounded MT Bold", sans-serif;
  }
  .canvas {
    position: relative;
    width: 1200px;
    height: 886px;
  }
  .sign {
    position: absolute;
    left: 0;
    top: 61px;
    width: 1200px;
    height: 763px;
    overflow: hidden;
    background: var(--sign-white);
  }
  .ice-cream-photo {
    position: absolute;
    inset: 0;
    background:
      radial-gradient(circle at 18% 30%, var(--photo-chocolate) 0 16%, transparent 17%),
      radial-gradient(circle at 52% 25%, var(--photo-peach) 0 17%, transparent 18%),
      radial-gradient(circle at 83% 12%, var(--photo-plum) 0 13%, transparent 14%),
      radial-gradient(circle at 93% 45%, #e8334a 0 13%, transparent 14%),
      radial-gradient(circle at 37% 65%, var(--photo-berry) 0 17%, transparent 18%),
      radial-gradient(circle at 72% 68%, var(--photo-lemon) 0 16%, transparent 17%),
      linear-gradient(160deg, #dfe9f2 0%, var(--photo-sky) 100%);
  }
  .sign-shapes {
    position: absolute;
    inset: 0;
    width: 1200px;
    height: 763px;
  }
  .brand-name {
    position: absolute;
    left: 62px;
    top: 528px;
    width: 600px;
    text-align: center;
    color: var(--ink);
    font-weight: 600;
    line-height: 1;
  }
  .brand-name__main {
    display: block;
    font-size: 92px;
    letter-spacing: 4px;
  }
  .brand-name__sub {
    display: block;
    margin-top: 18px;
    font-size: 44px;
    letter-spacing: 2px;
  }
  .distance {
    position: absolute;
    left: 745px;
    top: 650px;
    font-size: 90px;
    font-weight: 600;
    line-height: 1;
    color: var(--grape);
    letter-spacing: -1px;
  }
</style>
</head>
<body>
  <div class="canvas">
    <section class="sign" aria-label="Korrabel Ice Creamery roadside sign">
      <div class="ice-cream-photo" role="img" aria-label="Photograph of six scoops of ice cream in cones: chocolate, peach, plum, raspberry, strawberry and lemon, some topped with sprinkles"></div>

      <svg class="sign-shapes" viewBox="0 0 1126 716" preserveAspectRatio="none" aria-hidden="true">
        <path class="panel-white" fill="var(--sign-white)"
              d="M0,498 Q330,620 640,612 Q930,600 1126,498 L1126,716 L0,716 Z"/>
        <path class="swoosh-butter" fill="var(--butter)"
              d="M430,588 Q700,606 930,566 Q1060,534 1126,482 L1126,498 Q930,600 640,612 Q520,612 430,588 Z"/>
        <path class="swoosh-lime" fill="var(--lime)"
              d="M470,574 Q760,588 940,530 Q1070,476 1126,383 L1126,482 Q1060,534 930,566 Q700,602 470,574 Z"/>
        <g class="direction-arrow">
          <path fill="var(--grape)" d="M893,523 L945,523 L1002,618 L945,716 L893,716 L950,618 Z"/>
          <path fill="var(--grape-light)" d="M910,523 L945,523 L1002,618 L980,618 Z"/>
          <path fill="var(--grape)" d="M960,523 L1012,523 L1058,618 L1012,716 L960,716 L1006,618 Z"/>
          <path fill="var(--grape-light)" d="M977,523 L1012,523 L1058,618 L1036,618 Z"/>
        </g>
      </svg>

      <h1 class="brand-name">
        <span class="brand-name__main">KORRABEL</span>
        <span class="brand-name__sub">ICE CREAMERY</span>
      </h1>

      <p class="distance">17km</p>
    </section>
  </div>
</body>
</html>
```